Business card for medical clinic

I need an upmarket, modern medical/health business card for my clinic

Contact Information for Business Card

name, address, email, qr code

```html
<!DOCTYPE html>
<html lang="en">
<head>
<meta charset="utf-8">
<title>Meridian Care Partners – Business Card</title>
<link rel="stylesheet" href="https://fonts.googleapis.com/css2?family=Merriweather:wght@400;700&display=swap">
<style>
  :root {
    --backdrop-top: #3f9ac6;
    --backdrop-bottom: #1c7db3;
    --card: #ffffff;
    --brand-blue: #1f74b4;
    --brand-light: #2d9ad8;
    --ink: #3a3f45;
    --shadow: rgba(0, 40, 70, 0.35);
  }
  * { box-sizing: border-box; margin: 0; padding: 0; }
  html, body {
    width: 1200px;
    height: 876px;
    overflow: hidden;
  }
  body {
    background: linear-gradient(160deg, var(--backdrop-top), var(--backdrop-bottom));
    font-family: "Merriweather", Georgia, serif;
    color: var(--ink);
    position: relative;
  }
  .card {
    position: absolute;
    width: 520px;
    height: 300px;
    background: var(--card);
    box-shadow: 0 14px 30px var(--shadow);
  }
  .card--back { left: 50px; top: 288px; }
  .card--front { left: 630px; top: 288px; }

  .wordmark {
    display: flex;
    align-items: center;
    gap: 12px;
    color: var(--brand-blue);
    font-weight: 700;
    letter-spacing: 0.06em;
    text-transform: uppercase;
  }
  .wordmark__dot {
    border-radius: 50%;
    background: var(--brand-light);
    flex: none;
  }

  /* back: contact side */
  .card--back .wordmark { position: absolute; left: 34px; top: 34px; font-size: 15px; }
  .card--back .wordmark__dot { width: 22px; height: 22px; }

  .address {
    position: absolute;
    left: 34px;
    top: 122px;
    font-size: 11px;
    line-height: 1.7;
  }
  .person {
    position: absolute;
    right: 34px;
    top: 112px;
    text-align: right;
  }
  .person__name {
    color: var(--brand-blue);
    font-size: 17px;
    font-weight: 400;
    letter-spacing: 0.08em;
    text-transform: uppercase;
  }
  .person__role { font-size: 12px; margin-top: 4px; }

  .contacts {
    position: absolute;
    left: 210px;
    bottom: 30px;
    list-style: none;
    font-size: 12px;
    line-height: 1.9;
  }
  .contacts li { display: flex; align-items: center; gap: 8px; }
  .contacts svg { width: 12px; height: 12px; fill: var(--brand-blue); flex: none; }
  .contacts .phone { letter-spacing: 0.14em; }

  /* front: brand side */
  .card--front .wordmark {
    position: absolute;
    left: 0; right: 0; top: 130px;
    justify-content: center;
    font-size: 22px;
  }
  .card--front .wordmark__dot { width: 30px; height: 30px; }
</style>
</head>
<body>

<section class="card card--back" aria-label="Contact side">
  <div class="wordmark">
    <span class="wordmark__dot"></span>
    <span>Meridian Care Partners</span>
  </div>

  <address class="address" style="font-style: normal;">
    PO Box 418290<br>
    Cedar Falls, Alaska 99612
  </address>

  <div class="person">
    <h1 class="person__name">Daniel Hartwell</h1>
    <p class="person__role">Principal Consultant</p>
  </div>

  <ul class="contacts">
    <li>
      <svg viewBox="0 0 24 24" aria-hidden="true"><path d="M6.6 10.8a15 15 0 0 0 6.6 6.6l2.2-2.2a1 1 0 0 1 1-.25 11.4 11.4 0 0 0 3.6.57 1 1 0 0 1 1 1V20a1 1 0 0 1-1 1A17 17 0 0 1 3 4a1 1 0 0 1 1-1h3.5a1 1 0 0 1 1 1c0 1.25.2 2.45.57 3.57a1 1 0 0 1-.25 1z"/></svg>
      <span class="phone">+1-907-555-0142</span>
    </li>
    <li>
      <svg viewBox="0 0 24 24" aria-hidden="true"><path d="M2 5h20v14H2z M4 7v.4l8 5.2 8-5.2V7z" fill-rule="evenodd"/></svg>
      <span>info@meridiancarepartners.com</span>
    </li>
    <li>
      <svg viewBox="0 0 24 24" aria-hidden="true"><circle cx="12" cy="12" r="10"/><path d="M2 12h20M12 2c3 3 3 17 0 20M12 2c-3 3-3 17 0 20" stroke="#fff" stroke-width="1.5" fill="none"/></svg>
      <span>www.meridiancarepartners.com</span>
    </li>
  </ul>
</section>

<section class="card card--front" aria-label="Brand side">
  <div class="wordmark">
    <span class="wordmark__dot"></span>
    <span>Meridian Care Partners</span>
  </div>
</section>

</body>
</html>
```